Modern Business Card For A Digital Advertising Company

I'll be print on the Pell Prints Velour paper http://us.pellprints.com/products/velour/business-cards.html
Need's to be modern and use the color palette of the logo or gray scales. I think integrating the pixelation of the logo in to the card and having it wrap from one side to the other could be interesting. My company provides ad operations, web development, and number of other services to websites around the world. You can see my website at http://www.zantorhq.com
Contact info on the card needs to have
Owen Lasko
President
p.318.204.6637
owen@zantorhq.com
http://www.zantorhq.com
Doesn't necessarily need to be in that order
Website owners
Business

```html
<!DOCTYPE html>
<html lang="en">
<head>
<meta charset="utf-8">
<title>Zantor HQ – Business Card</title>
<link rel="stylesheet" href="https://fonts.googleapis.com/css2?family=Arimo:wght@400;700&display=swap">
<style>
  :root {
    --backdrop: #3a3b3d;
    --card-white: #ffffff;
    --green-light: #8cc63f;
    --green-mid: #76ad3c;
    --green-dark: #5b8a3a;
    --rule-dark: #3b3b3b;
    --text-grey: #4a4a4a;
    --icon-green: #7ab648;
  }
  * { box-sizing: border-box; margin: 0; padding: 0; }
  html, body {
    width: 1200px; height: 450px; overflow: hidden;
    background: var(--backdrop);
    font-family: "Arimo", Arial, sans-serif;
  }
  .stage { position: relative; width: 1200px; height: 450px; }

  .card {
    position: absolute; top: 80px;
    width: 524px; height: 298px;
    border-radius: 24px; overflow: hidden;
  }

  /* Front */
  .card-front { left: 58px; background: var(--card-white); }
  .front-band {
    position: absolute; left: 0; top: 0; bottom: 0; width: 50px;
    background: linear-gradient(90deg, var(--green-light), var(--green-mid));
  }
  .front-rule {
    position: absolute; left: 52px; top: 0; bottom: 0; width: 5px;
    background: var(--rule-dark);
  }
  .brand {
    position: absolute; left: 92px; top: 120px;
    display: flex; align-items: center; gap: 8px;
    color: var(--green-light); font-weight: 700; font-size: 27px;
    letter-spacing: 1px;
  }
  .brand-square { width: 14px; height: 14px; background: var(--green-light); }
  .holder {
    position: absolute; left: 292px; top: 88px;
    color: var(--green-light); font-size: 20px; font-weight: 700;
  }
  .holder .role { font-weight: 400; font-size: 16px; }
  .contact {
    position: absolute; left: 85px; top: 218px;
    list-style: none; color: var(--text-grey); font-size: 15px; line-height: 22.5px;
  }
  .contact li { display: flex; align-items: center; gap: 5px; }
  .contact svg { width: 10px; height: 10px; flex: none; }

  /* Back */
  .card-back {
    left: 622px;
    background: linear-gradient(90deg, var(--green-light), var(--green-dark));
  }
  .back-brand {
    position: absolute; left: 0; right: 0; top: 100px;
    display: flex; justify-content: center; align-items: center; gap: 14px;
    color: var(--card-white); font-weight: 700; font-size: 54px; letter-spacing: 2px;
  }
  .back-brand .brand-square { width: 26px; height: 26px; background: var(--card-white); }
  .back-url {
    position: absolute; left: 0; right: 0; top: 234px; text-align: center;
    color: var(--card-white); font-size: 19px; letter-spacing: 1px;
  }
</style>
</head>
<body>
<main class="stage">
  <section class="card card-front">
    <div class="front-band"></div>
    <div class="front-rule"></div>
    <div class="brand"><span class="brand-square"></span>ZANTOR HQ</div>
    <p class="holder">Owen Lasko, <span class="role">President</span></p>
    <ul class="contact">
      <li>
        <svg viewBox="0 0 10 10" aria-hidden="true"><circle cx="5" cy="5" r="4.3" fill="none" stroke="var(--icon-green)" stroke-width="1.2"/><path d="M3.4 2.6l1 1-.6.7c.4.8 1 1.4 1.8 1.8l.7-.6 1 1-.8.8C4.8 7 3 5.2 2.6 3.4z" fill="var(--icon-green)"/></svg>
        318.204.6637
      </li>
      <li>
        <svg viewBox="0 0 10 10" aria-hidden="true"><rect x="0.5" y="2" width="9" height="6.5" rx="1" fill="var(--icon-green)"/><path d="M0.8 2.5L5 5.8l4.2-3.3" fill="none" stroke="#fff" stroke-width="0.9"/></svg>
        owen@zantorhq.com
      </li>
      <li>
        <svg viewBox="0 0 10 10" aria-hidden="true"><circle cx="5" cy="5" r="4.5" fill="var(--icon-green)"/><path d="M0.5 5h9M5 0.5c-2 2.5-2 6.5 0 9M5 0.5c2 2.5 2 6.5 0 9" fill="none" stroke="#fff" stroke-width="0.6"/></svg>
        www.zantorhq.com
      </li>
    </ul>
  </section>

  <section class="card card-back">
    <div class="back-brand"><span class="brand-square"></span>ZANTOR HQ</div>
    <p class="back-url">www.zantorhq.com</p>
  </section>
</main>
</body>
</html>
```